Wandering Rooms Stationary Set

Wandering Rooms is a bespoke interior design firm set to provide services to VIP clients with elegance and minimalism is the main theme for our stationary set. We require a full stationary set covering A4 letterhead, A4 & A3 envelopes, business cards, USB's, CDs, email signature and any other item the designer sees fit. logo is already designed and finalized, and we require the designer to use it as is without modifying the logo.

Address to be used on letterhead / business cards ...etc shall be as follows:

Phone : +971 2 518 2047
P.O. Box : 309186
Address: Block C&D, Bldg. 47, Court 12, Abu Dhabi, United Arab Emirates
Website: www.wanderingrooms-example.com

Target Market(s)

VIP Clients

Industry/Entity Type

Interior Design

Font styles to use
Other font styles liked:
• something to be unique

Colors

Designer to choose colors to be used in the design.

Requirements
Must have
• Elegant, minimalistic
Nice to have
• Simple yet elegant design having a sharp yet clean cut format
Should not have
• No additional colours, just colours that are used in the logo (silver, black or gold)

```html
<!DOCTYPE html>
<html lang="en">
<head>
<meta charset="utf-8">
<title>Wandering Rooms Stationery</title>
<link href="https://fonts.googleapis.com/css2?family=Questrial&family=EB+Garamond:wght@500&display=swap" rel="stylesheet">
<style>
  :root {
    --ink: #262626;
    --band: #2b2b2b;
    --paper: #ffffff;
    --silver: #c9c9c9;
    --backdrop: #e6e5e3;
    --text: #3a3a3a;
  }
  * { margin: 0; padding: 0; box-sizing: border-box; }
  html, body { width: 1200px; height: 800px; overflow: hidden; }
  body {
    background: var(--backdrop);
    font-family: "Questrial", "Century Gothic", sans-serif;
    color: var(--text);
    position: relative;
  }
  .letterhead {
    position: absolute;
    left: 330px; top: 20px;
    width: 537px; height: 760px;
    background: var(--paper);
    box-shadow: 0 2px 10px rgba(0,0,0,0.12);
  }
  .brand-tab {
    position: absolute;
    left: 170px; top: 0;
    width: 206px; height: 122px;
    background: var(--band);
    border-radius: 0 0 14px 14px;
    display: flex; align-items: center; justify-content: center;
  }
  .brand-name {
    font-family: "Questrial", sans-serif;
    font-size: 21px;
    letter-spacing: 2px;
    text-transform: uppercase;
    color: var(--silver);
    text-align: center;
    line-height: 1.3;
  }
  .letter-body {
    position: absolute;
    left: 63px; top: 172px;
    width: 422px;
    font-size: 10.4px;
    line-height: 17.4px;
  }
  .salutation { margin-bottom: 17px; }
  .letter-body p.paragraph { text-align: justify; hyphens: auto; margin-bottom: 17px; }
  .signatory { position: absolute; left: 63px; top: 538px; }
  .signatory-name { font-size: 13.5px; color: var(--ink); }
  .signatory-role { font-size: 8.5px; margin-top: 6px; }
  .footer-address {
    position: absolute;
    left: 0; right: 0; top: 706px;
    text-align: center;
    font-family: "EB Garamond", serif;
    font-weight: 500;
    font-size: 9px;
    color: var(--ink);
  }
  .footer-band {
    position: absolute;
    left: 0; right: 0; bottom: 0;
    height: 32px;
    background: var(--band);
    border-radius: 14px 14px 0 0;
    display: flex; align-items: center; justify-content: center; gap: 18px;
    font-family: "EB Garamond", serif;
    font-size: 10.5px;
    color: var(--silver);
  }
  .contact-item { display: flex; align-items: center; gap: 5px; }
  .contact-item svg { width: 8px; height: 8px; }
  .business-card {
    position: absolute;
    width: 230px; height: 140px;
    background: var(--paper);
    box-shadow: 0 2px 8px rgba(0,0,0,0.12);
    display: flex; align-items: center; justify-content: center;
  }
  .business-card .brand-name { color: var(--ink); font-size: 19px; }
  .card-top { left: 920px; top: 90px; }
  .card-bottom { left: 920px; top: 270px; }
</style>
</head>
<body>
  <section class="letterhead">
    <div class="brand-tab"><div class="brand-name">Wandering<br>Rooms</div></div>

    <div class="letter-body">
      <p class="salutation">Hello Sir/Mam,</p>
      <p class="paragraph">Lorem ipsum dolor sit amet, consectetur adipiscing elit. Donec orci purus, luctus vitae dignissim eu, iaculis sed purus. Vivamus faucibus, ipsum nec aliquet viverra, leo mauris condimentum ligula, sit amet sagittis enim ligula quis arcu. Nam egestas tortor id nisi porttitor mattis. In tortor ante, ultricies in suscipit a, tempus non massa. Vivamus et auctor mi. Fusce vel massa nulla. Phasellus nec eros mauris, et scelerisque orci. Donec malesuada orci vitae nulla accumsan porta a id massa.</p>
      <p class="paragraph">Quisque accumsan iaculis magna sit amet fringilla. Maecenas consequat, magna eget tincidunt semper, odio nibh rutrum mi, id feugiat ante nisi eu risus. Vestibulum nunc orci, rhoncus a placerat in, ultricies in mi. Cras mattis varius eros, vel fringilla nisi suscipit eget. Quisque scelerisque sagittis nulla at porttitor. Mauris a justo et tellus interdum tristique. Sed id augue vitae urna euismod commodo aliquet a quam. Pellentesque arcu velit, cursus et malesuada ut, consequat et diam. Nullam erat sem, rhoncus id ullamcorper vitae, rhoncus et arcu. In ultricies ultricies nulla, el fringilla nisi suscipit eget. Quisque scelerisque sagittis nulla at porttitor. Mauris a justo et tellus interdum tristique. Sed id augue vitae urna euismod commodo aliquet a quam. Pellentesque arcu velit, cursus et malesuada ut, consequat et diam. Nullam erat sem, rhoncus id ullamcorper vitae, rhoncus et arcu. In ultricies ultricies nulla,</p>
    </div>

    <div class="signatory">
      <div class="signatory-name">Laith Marwan</div>
      <div class="signatory-role">Co-Founder &amp; CEO</div>
    </div>

    <div class="footer-address">Block C&amp;D, Bldg. 47, Court 12, Abu Dhabi, United Arab Emirates</div>
    <div class="footer-band">
      <span class="contact-item"><svg viewBox="0 0 8 8"><circle cx="4" cy="4" r="4" fill="#8a8a8a"/></svg>+971 2 518 2047</span>
      <span class="contact-item"><svg viewBox="0 0 8 8"><circle cx="4" cy="4" r="4" fill="#8a8a8a"/></svg>studio@wanderingrooms-example.com</span>
      <span class="contact-item"><svg viewBox="0 0 8 8"><circle cx="4" cy="4" r="4" fill="#8a8a8a"/></svg>P.O. Box : 309186</span>
    </div>
  </section>

  <div class="business-card card-top"><div class="brand-name">Wandering<br>Rooms</div></div>
  <div class="business-card card-bottom"><div class="brand-name">Wandering<br>Rooms</div></div>
</body>
</html>
```